Business Card Design for Software Development Company

I am looking for a business card design the incorporates my new logo (attached below).

Key information to include:
Name: Martin Quelbrook
Title: CEO
Email: martin@brightwellcivic.example
Phone: 555-218-9403
Website: www.brightwellcivic.example

NOTE: This design should be easy to edit so that we can order cards for different members of our team.

```html
<!DOCTYPE html>
<html lang="en">
<head>
<meta charset="utf-8">
<title>Brightwell Civic – Business Card</title>
<link href="https://fonts.googleapis.com/css2?family=Montserrat:wght@400;500;700&display=swap" rel="stylesheet">
<style>
  :root {
    --backdrop: #1d1d1d;
    --card: #f4f4f4;
    --navy: #36405a;
    --orange: #e57d24;
    --amber: #e8a31f;
    --crimson: #a01f27;
    --ink: #2a2a2a;
  }
  * { box-sizing: border-box; margin: 0; padding: 0; }
  html, body {
    width: 1200px; height: 1059px; overflow: hidden;
    background: var(--backdrop);
    font-family: "Montserrat", sans-serif;
  }
  .card {
    position: absolute;
    background: var(--card);
    border-radius: 18px;
    overflow: hidden;
  }
  .card--front { left: 257px; top: 89px; width: 687px; height: 390px; }
  .card--back  { left: 253px; top: 546px; width: 694px; height: 394px; }

  .accent-tab {
    position: absolute; left: 0; top: 188px;
    width: 17px; height: 40px;
    background: var(--navy);
    border-radius: 0 4px 4px 0;
  }
  .brand-block {
    position: absolute; left: 430px; top: 30px;
    width: 150px; height: 150px;
    background: var(--orange);
  }
  .holder { position: absolute; left: 41px; top: 180px; }
  .holder__name {
    font-weight: 700; font-size: 25px; letter-spacing: -0.2px;
    color: var(--navy); line-height: 1;
  }
  .holder__name .surname { color: var(--orange); }
  .holder__title {
    font-weight: 400; font-size: 17px; color: var(--ink);
    margin-top: 8px;
  }
  .contacts {
    position: absolute; left: 41px; top: 263px;
    list-style: none;
  }
  .contacts li {
    display: flex; align-items: center; gap: 8px;
    height: 32.5px;
    font-size: 17px; color: var(--ink);
  }
  .contacts svg { width: 14px; height: 14px; flex: none; }

  .brand {
    position: absolute; left: 0; right: 0; top: 0; bottom: 0;
    display: flex; align-items: center; justify-content: center; gap: 16px;
  }
  .brand__square { width: 40px; height: 40px; background: var(--orange); }
  .brand__name {
    font-weight: 700; font-size: 48px; color: var(--navy);
    letter-spacing: -0.5px;
  }
</style>
</head>
<body>
  <section class="card card--front">
    <div class="accent-tab"></div>
    <div class="brand-block"></div>
    <div class="holder">
      <p class="holder__name">MARTIN <span class="surname">QUELBROOK</span></p>
      <p class="holder__title">CEO</p>
    </div>
    <ul class="contacts">
      <li>
        <svg viewBox="0 0 14 14"><path fill="#e8a31f" d="M1 5c0-2 3-3 6-3s6 1 6 3v1h-3V5H4v1H1z"/><rect x="3" y="7" width="8" height="5" rx="1" fill="#e8a31f"/></svg>
        555-218-9403
      </li>
      <li>
        <svg viewBox="0 0 14 14"><rect x="1" y="3" width="12" height="9" fill="#a01f27"/><path d="M1 3l6 5 6-5" fill="none" stroke="#f4f4f4" stroke-width="1.2"/></svg>
        martin@brightwellcivic.example
      </li>
      <li>
        <svg viewBox="0 0 14 14"><circle cx="7" cy="7" r="6" fill="#e57d24"/><path d="M4 4c2 0 2 2 4 2s1 3-1 3-1 3-2 3M9 3c0 1 2 1 2 3" fill="none" stroke="#f4f4f4" stroke-width="1"/></svg>
        www.brightwellcivic.example
      </li>
    </ul>
  </section>

  <section class="card card--back">
    <div class="brand">
      <span class="brand__square"></span>
      <span class="brand__name">Brightwell Civic</span>
    </div>
  </section>
</body>
</html>
```